Lanternfield Drinks business cards

We need a business card design for our new logo. The company is modern, progressive, professional, yet approachable. The key products are ready to drink bottles and cans of coffee based beverages.
These cards will be a critical part of the first impression made by our sales organization, business development team, and all external facing personnel.
Card can be a vertical or horizontal orientation.

Target Market(s)

Customers, suppliers, business partners

Industry/Entity Type

Business

Contact Information for Business Card

Business cards should feature Company Name and Logo.

Font styles to use
Serif

Colors

Designer to choose colors to be used in the design.

Requirements
Must have
• Strong readability of Name, phone #, mobile number and email address.
• Job title, website url, Street Address, and other details can be secondary level readability.
Nice to have
• High impact, simplistic quality design.
• Ok to utilize the 'H in the box' separate from the company name

```html
<!DOCTYPE html>
<html lang="en">
<head>
<meta charset="utf-8">
<title>Lanternfield Drinks – Business Cards</title>
<link href="https://fonts.googleapis.com/css2?family=Lato:wght@400;700&display=swap" rel="stylesheet">
<style>
  :root {
    --backdrop: #8a8a8a;
    --brand-orange: #f05a2c;
    --accent-amber: #f4a21c;
    --paper: #ffffff;
    --ink-light: #ffffff;
  }
  html, body {
    margin: 0;
    padding: 0;
    overflow: hidden;
  }
  .canvas {
    position: relative;
    width: 1200px;
    height: 900px;
    background: var(--backdrop);
    font-family: "Lato", Arial, sans-serif;
    overflow: hidden;
  }
  .card {
    position: absolute;
    top: 170px;
    width: 346px;
    height: 560px;
    box-shadow: 3px 4px 6px rgba(0,0,0,0.45);
  }
  .card--front {
    left: 260px;
    background: var(--brand-orange);
    color: var(--ink-light);
    text-align: center;
  }
  .card--back {
    left: 632px;
    background: var(--paper);
  }

  /* Front card: brand block */
  .brand-block {
    position: absolute;
    top: 40px;
    left: 0;
    width: 100%;
  }
  .brand-square {
    width: 78px;
    height: 78px;
    margin: 0 auto;
    border: 7px solid var(--ink-light);
    box-sizing: border-box;
  }
  .brand-name {
    margin-top: 18px;
    font-weight: 700;
    font-size: 20px;
    letter-spacing: 1px;
  }

  /* Front card: person and contact */
  .person {
    position: absolute;
    top: 310px;
    left: 0;
    width: 100%;
  }
  .person__name {
    font-weight: 700;
    font-size: 22px;
    line-height: 26px;
  }
  .person__title {
    font-size: 16px;
    line-height: 22px;
  }
  .divider {
    width: 200px;
    height: 1px;
    background: rgba(255,255,255,0.75);
    margin: 0 auto;
  }
  .divider--upper { position: absolute; top: 370px; left: 73px; }
  .divider--lower { position: absolute; top: 468px; left: 73px; }
  .contact {
    position: absolute;
    top: 382px;
    left: 0;
    width: 100%;
    font-size: 15.5px;
    line-height: 19px;
  }
  .address {
    position: absolute;
    top: 477px;
    left: 0;
    width: 100%;
    font-size: 15.5px;
    line-height: 20px;
  }

  /* Back card */
  .back-square {
    position: absolute;
    left: 52px;
    top: 213px;
    width: 134px;
    height: 134px;
    border: 6px solid var(--brand-orange);
    box-sizing: border-box;
  }
  .back-name {
    position: absolute;
    left: 6px;
    top: 258px;
    width: 460px;
    height: 44px;
    line-height: 44px;
    text-align: center;
    transform: rotate(-90deg);
    font-weight: 700;
    font-size: 35px;
    letter-spacing: 1px;
    color: var(--brand-orange);
    white-space: nowrap;
  }
  .back-rule {
    position: absolute;
    left: 283px;
    top: 52px;
    width: 3px;
    height: 458px;
    background: var(--accent-amber);
  }
</style>
</head>
<body>
<div class="canvas">
  <section class="card card--front">
    <div class="brand-block">
      <div class="brand-square"></div>
      <div class="brand-name">LANTERNFIELD DRINKS</div>
    </div>
    <div class="person">
      <div class="person__name">LORUM SMITH</div>
      <div class="person__title">MANAGING DIRECTOR</div>
    </div>
    <div class="divider divider--upper"></div>
    <div class="contact">
      P: 888 555 4433<br>
      M: 888 444 0000<br>
      E: info@webname.com<br>
      W: www.webname.com
    </div>
    <div class="divider divider--lower"></div>
    <div class="address">
      421, Address line here,<br>
      Dummy Code, 45452<br>
      Country Name
    </div>
  </section>

  <section class="card card--back">
    <div class="back-square"></div>
    <div class="back-name">LANTERNFIELD DRINKS</div>
    <div class="back-rule"></div>
  </section>
</div>
</body>
</html>
```